Professional and creative business card design for recruiting service providers

Our company supports German medium-sized companies in filling vacancies promptly. For this we use social media marketing and bring our customers into the visibility.

We want a professional but also creative design for our business cards.

Please look at lindqvar-staff.de to get an impression of our CI.

Target Market(s)

Small and medium-sized companies in Germany from the industry

Industry/Entity Type

Industrie, Handwerk

Contact Information for Business Card

Name, Position, Telefonnummer, Email, Website

Colors
EE7325
F08F49
F5BC92
FAE3D3
FDF4ED

Requirements
Must have
• A picture of the employee and in the style of www.lindqvar-staff.de

```html
<!DOCTYPE html>
<html lang="en">
<head>
<meta charset="utf-8">
<title>Lindqvar &amp; Staff – Business Card</title>
<link rel="stylesheet" href="https://fonts.googleapis.com/css2?family=Poppins:wght@400;500;600;700&display=swap">
<style>
  :root {
    --orange: #ef6a2c;
    --ink: #1b1c1e;
    --ink-soft: #2a2b2e;
    --white: #ffffff;
    --backdrop: #2b2b2d;
    --rule: #8a8a8a;
  }
  * { box-sizing: border-box; margin: 0; padding: 0; }
  html, body {
    width: 1200px; height: 1108px; overflow: hidden;
    background: var(--backdrop);
    font-family: "Poppins", sans-serif;
  }
  .stage { position: relative; width: 1200px; height: 1108px; }
  .card {
    position: absolute; top: 214px; width: 420px; height: 680px;
    border-radius: 18px; overflow: hidden;
  }
  .card--front { left: 150px; background: var(--ink); }
  .card--back {
    left: 630px;
    background: linear-gradient(160deg, #4a4a4c 0%, #1f1f21 45%, #0d0d0e 100%);
  }
  .portrait {
    height: 330px;
    background:
      radial-gradient(ellipse 45% 55% at 55% 80%, #1f2027 0%, #2a2b31 55%, transparent 75%),
      linear-gradient(180deg, #dcdcdf 0%, #cfcfd2 60%, #b9b9bc 100%);
  }
  .details {
    height: 190px; padding-top: 16px; text-align: center; color: var(--white);
  }
  .details__name {
    color: var(--orange); font-weight: 600; font-size: 30px;
    letter-spacing: 1px; line-height: 1.1;
  }
  .details__role { font-size: 16px; font-weight: 400; margin-top: 2px; }
  .details__divider {
    display: flex; align-items: center; justify-content: center;
    gap: 8px; margin: 12px 0 8px;
  }
  .details__divider::before, .details__divider::after {
    content: ""; width: 72px; height: 1px; background: var(--rule);
  }
  .icon {
    width: 28px; height: 28px; border-radius: 5px; background: var(--orange);
    display: flex; align-items: center; justify-content: center;
  }
  .details__contacts { list-style: none; font-size: 15px; line-height: 1.45; }
  .brand-strip {
    height: 160px; background: var(--white);
    display: flex; align-items: center; justify-content: center; gap: 16px;
  }
  .brand-strip__mark { width: 46px; height: 46px; background: var(--orange); }
  .brand-strip__name {
    color: var(--ink); font-weight: 700; font-size: 30px;
    letter-spacing: 2px; line-height: 1.05;
  }
  .pattern { position: absolute; inset: 0; }
  .brand-badge {
    position: absolute; left: 0; right: 0; top: 440px; text-align: center;
    color: var(--white); font-weight: 700; font-size: 20px; letter-spacing: 2px;
  }
</style>
</head>
<body>
<main class="stage">
  <article class="card card--front">
    <div class="portrait" role="img" aria-label="Portrait photo of the managing director seated in an office chair"></div>
    <section class="details">
      <h1 class="details__name">MATTHIAS KERNER</h1>
      <p class="details__role">Managing Director</p>
      <div class="details__divider">
        <span class="icon">
          <svg width="16" height="16" viewBox="0 0 24 24"><path fill="#1b1c1e" d="M6.6 10.8a15 15 0 0 0 6.6 6.6l2.2-2.2c.3-.3.7-.4 1-.2 1.1.4 2.3.6 3.6.6.6 0 1 .4 1 1V20c0 .6-.4 1-1 1A17 17 0 0 1 3 4c0-.6.4-1 1-1h3.5c.6 0 1 .4 1 1 0 1.3.2 2.5.6 3.6.1.3 0 .7-.2 1z"/></svg>
        </span>
        <span class="icon">
          <svg width="16" height="16" viewBox="0 0 24 24"><rect x="3" y="6" width="18" height="12" fill="none" stroke="#1b1c1e" stroke-width="2"/><path d="M3 6l9 7 9-7" fill="none" stroke="#1b1c1e" stroke-width="2"/></svg>
        </span>
        <span class="icon">
          <svg width="16" height="16" viewBox="0 0 24 24"><circle cx="12" cy="12" r="9" fill="none" stroke="#1b1c1e" stroke-width="2"/><path d="M3 12h18M12 3c3 3 3 15 0 18M12 3c-3 3-3 15 0 18" fill="none" stroke="#1b1c1e" stroke-width="1.6"/></svg>
        </span>
      </div>
      <ul class="details__contacts">
        <li>030-987 654 321</li>
        <li>info@lindqvar-staff.de</li>
        <li>www.lindqvar-staff.de</li>
      </ul>
    </section>
    <footer class="brand-strip">
      <span class="brand-strip__mark"></span>
      <p class="brand-strip__name">LINDQVAR<br>&amp; STAFF</p>
    </footer>
  </article>

  <article class="card card--back">
    <div class="pattern" role="img" aria-label="Glossy tone-on-tone repeating geometric pattern across the card back"></div>
    <p class="brand-badge">LINDQVAR &amp; STAFF</p>
  </article>
</main>
</body>
</html>
```